Makers' Hollow - Landing page for small and large screen

Makers’ Hollow gives you the space you need to take your side project from idea to reality.

With three days of focused work, it’s a place for you iron out the details of your business idea away from the distractions of the city.

The full copy and structure is here:
https://www.makershollow.co.uk/landing

What it needs, a touch of colour.

Target Market(s)

25-35 working in digital industry, software developer, a UI or UX designer

Number of Pages Required

1 page

Font styles to use
Sans Serif

Colors
0292cd
33b8a4
86cfc6
fdf9cf
ec1f27

Requirements
Should not have
• gradients or too much images

```html
<!DOCTYPE html>
<html lang="en">
<head>
<meta charset="utf-8">
<title>Makers' Hollow</title>
<link href="https://fonts.googleapis.com/css2?family=Lato:wght@300;400;700;900&display=swap" rel="stylesheet">
<style>
:root{
  --blue:#0292cd;
  --teal:#33b8a4;
  --teal-light:#86cfc6;
  --cream:#fdf9cf;
  --red:#ec1f27;
  --ink:#1f2126;
  --text:#555a60;
  --muted:#8a8f95;
  --line:#e4e6e8;
  --footer:#23252a;
  --white:#ffffff;
}
*{box-sizing:border-box;margin:0;padding:0}
html,body{width:1200px;height:3212px;overflow:hidden}
body{font-family:"Lato",Arial,sans-serif;color:var(--text);background:var(--white)}
section,header,footer{position:relative;width:1200px}

/* Hero */
.hero{height:560px;overflow:hidden}
.hero-photo{position:absolute;inset:0;background:linear-gradient(160deg,#3d3a38 0%,#2a2523 45%,#4a3f36 75%,#1f1c1b 100%)}
.hero-shade{position:absolute;inset:0;background:rgba(0,0,0,.28)}
.brand{position:absolute;left:40px;top:30px;color:var(--white)}
.brand-name{font-size:34px;font-weight:700;letter-spacing:.3px}
.brand-tag{font-size:15px;font-weight:400;opacity:.85;margin-top:2px;letter-spacing:.5px}
.menu-btn{position:absolute;right:40px;top:40px;width:52px;height:52px;border:2px solid var(--white);border-radius:50%}
.hero-title{position:absolute;left:0;right:0;top:360px;text-align:center;color:var(--white);font-size:58px;font-weight:700}
.hero-arrow{position:absolute;left:574px;top:436px}

/* Section titles */
.section-title{text-align:center;font-size:46px;font-weight:700;color:var(--ink)}

/* About */
.about{height:712px;padding-top:92px}
.about-lead{text-align:center;font-size:19px;color:var(--ink);margin-top:28px}
.about-copy{width:780px;margin:26px auto 0;text-align:center;font-size:15px;line-height:26px;color:var(--muted)}
.roles{display:flex;justify-content:center;gap:170px;margin-top:46px}
.role{width:180px;text-align:center}
.role-badge{margin:0 auto}
.role-name{font-size:21px;font-weight:700;color:var(--ink);margin-top:14px}
.about-copy.second{margin-top:34px}

/* Focus band */
.focus{height:328px;background:var(--teal);color:var(--white);text-align:center;padding-top:68px}
.focus-title{font-size:46px;font-weight:700}
.focus-copy{width:820px;margin:22px auto 0;font-size:15px;line-height:25px;opacity:.9}
.btn{display:inline-block;border-radius:30px;font-size:14px;font-weight:700;letter-spacing:.6px;text-transform:uppercase}
.btn-light{margin-top:22px;padding:12px 26px;background:var(--white);color:var(--teal)}

/* Perks */
.perks{height:584px;padding-top:130px}
.perk-row{position:relative;display:flex;justify-content:center;gap:28px;margin-top:62px}
.perk{width:236px;height:220px;background:var(--white);box-shadow:0 2px 10px rgba(0,0,0,.12);padding:30px 26px;position:relative}
.perk::before{content:"";position:absolute;top:0;right:0;width:100px;height:5px;background:var(--red)}
.perk.active{background:var(--blue);color:var(--white)}
.perk.active::before{display:none}
.perk-text{font-size:17px;line-height:25px;margin-top:22px;color:var(--text)}
.perk.active .perk-text{color:var(--white)}
.perk-dot{position:absolute;left:26px;bottom:28px}
.slider-arrow{position:absolute;top:92px}
.slider-arrow.prev{left:42px}
.slider-arrow.next{right:42px}
.divider{position:absolute;left:150px;right:150px;bottom:12px;height:1px;background:var(--line)}

/* Organisers */
.team{height:516px;padding-top:112px}
.team-row{display:flex;justify-content:center;gap:50px;margin-top:60px}
.member{width:462px;height:182px;box-shadow:0 2px 10px rgba(0,0,0,.1);display:flex;align-items:center;padding:0 28px;gap:26px}
.member-photo{width:128px;height:128px;border-radius:50%;flex:none}
.member-photo.one{background:linear-gradient(135deg,#3d4a55,#1d2429)}
.member-photo.two{background:linear-gradient(135deg,#d9c1a6,#6b4f3a)}
.member-name{font-size:17px;font-weight:700;color:var(--ink);letter-spacing:.6px;text-transform:uppercase}
.member-bio{font-size:14px;line-height:21px;color:var(--muted);margin-top:8px}
.member-link{display:inline-block;margin-top:10px;font-size:13px;font-weight:700;color:var(--blue);border-bottom:2px solid var(--blue);text-transform:uppercase}

/* Feedback band */
.feedback{height:380px;background:var(--teal);color:var(--white);text-align:center;padding-top:84px}
.feedback-title{font-size:46px;font-weight:700}
.feedback-copy{width:520px;margin:20px auto 0;font-size:17px;line-height:25px;font-weight:700}
.btn-red{margin-top:30px;padding:14px 28px;background:var(--red);color:var(--white)}

/* Footer */
.site-footer{height:172px;background:var(--footer);color:#c9cbce;padding:52px 58px 0}
.contact{font-size:14px;display:flex;gap:22px;align-items:center}
.contact span.sep{width:1px;height:16px;background:#6d7076}
.legal{font-size:13px;margin-top:18px;color:#9a9da2;display:flex;gap:14px;align-items:center}
.social{position:absolute;right:58px;top:56px;display:flex;gap:12px}
.social span{width:44px;height:44px;border:2px solid #c9cbce;border-radius:50%}
</style>
</head>
<body>

<header class="hero">
  <div class="hero-photo" role="img" aria-label="Photo of a man in a suit working on a laptop in a dim modern office"></div>
  <div class="hero-shade"></div>
  <div class="brand">
    <div class="brand-name">Makers’ Hollow</div>
    <div class="brand-tag">create. connect. collaborate</div>
  </div>
  <div class="menu-btn">
    <svg width="48" height="48" viewBox="0 0 48 48"><g stroke="#fff" stroke-width="2.5" stroke-linecap="round"><line x1="16" y1="18" x2="32" y2="18"/><line x1="16" y1="24" x2="32" y2="24"/><line x1="16" y1="30" x2="32" y2="30"/></g></svg>
  </div>
  <h1 class="hero-title">Create. Connect. Collaborate</h1>
  <svg class="hero-arrow" width="52" height="44" viewBox="0 0 52 44"><g fill="none" stroke="#fff" stroke-width="3" stroke-linecap="round" stroke-linejoin="round"><polyline points="8,8 26,22 44,8"/><polyline points="8,22 26,36 44,22"/></g></svg>
</header>

<section class="about">
  <h2 class="section-title">About Makers’ Hollow</h2>
  <p class="about-lead">Makers’ Hollow gives you the space you need to take your side project from idea to reality.</p>
  <p class="about-copy">Calling all creatives! Whether you’re a software developer, a UI or UX designer, a product creator or an artist, you’ll know only too well that good work rarely materialises when you’re in the wrong environment.</p>
  <div class="roles">
    <div class="role">
      <svg class="role-badge" width="120" height="132" viewBox="0 0 120 132"><circle cx="60" cy="60" r="56" fill="#e6f4fa"/><path d="M48 112 L60 128 L72 112 Z" fill="#e6f4fa"/><circle cx="60" cy="60" r="44" fill="var(--blue)"/><g fill="none" stroke="#fff" stroke-width="3.5" stroke-linecap="round" stroke-linejoin="round"><polyline points="46,48 34,60 46,72"/><polyline points="74,48 86,60 74,72"/><line x1="64" y1="44" x2="56" y2="76"/></g></svg>
      <div class="role-name">Software Developer</div>
    </div>
    <div class="role">
      <svg class="role-badge" width="120" height="132" viewBox="0 0 120 132"><circle cx="60" cy="60" r="56" fill="#e6f4fa"/><path d="M48 112 L60 128 L72 112 Z" fill="#e6f4fa"/><circle cx="60" cy="60" r="44" fill="var(--blue)"/><g fill="none" stroke="#fff" stroke-width="3.5" stroke-linejoin="round"><rect x="38" y="42" width="44" height="32" rx="3"/><line x1="52" y1="82" x2="68" y2="82"/><line x1="60" y1="74" x2="60" y2="82"/></g></svg>
      <div class="role-name">UI or UX Designer</div>
    </div>
    <div class="role">
      <svg class="role-badge" width="120" height="132" viewBox="0 0 120 132"><circle cx="60" cy="60" r="56" fill="#e6f4fa"/><path d="M48 112 L60 128 L72 112 Z" fill="#e6f4fa"/><circle cx="60" cy="60" r="44" fill="var(--blue)"/><g fill="none" stroke="#fff" stroke-width="3.5" stroke-linejoin="round"><path d="M60 38 L82 50 L82 72 L60 84 L38 72 L38 50 Z"/><polyline points="38,50 60,62 82,50"/><line x1="60" y1="62" x2="60" y2="84"/></g></svg>
      <div class="role-name">Product Creator</div>
    </div>
  </div>
  <p class="about-copy second">Phones buzzing, emails pinging, calls incoming… distractions are everywhere — and they do nothing for your motivation. So, if you have a seed of a business idea and need to isolate some focus, this retreat is for you. Or maybe you’ve created a product, sought a patron and you’re ready — and raring — to go.</p>
</section>

<section class="focus">
  <h2 class="focus-title">Three Days of Focused Work</h2>
  <p class="focus-copy">Whatever stage your side hustle is at, we’re here to help it thrive. Our warm and friendly retreat is just that: a place to create, connect and collaborate with likeminded folks. It’s a calm destination, with healthy meals and snacks, and all the feedback you need to power on through.</p>
  <span class="btn btn-light">Join now ➜</span>
</section>

<section class="perks">
  <h2 class="section-title">Join The Retreat &amp; Enjoy</h2>
  <div class="perk-row">
    <div class="perk active">
      <svg width="40" height="40" viewBox="0 0 40 40"><g fill="none" stroke="#fff" stroke-width="2.5"><rect x="4" y="8" width="32" height="28" rx="2"/><line x1="4" y1="16" x2="36" y2="16"/><line x1="12" y1="4" x2="12" y2="11"/><line x1="28" y1="4" x2="28" y2="11"/></g></svg>
      <p class="perk-text">Three full days of distraction-free work.</p>
      <svg class="perk-dot" width="18" height="18" viewBox="0 0 18 18"><circle cx="9" cy="9" r="9" fill="#fff"/><path d="M7 5 L11 9 L7 13" fill="none" stroke="var(--blue)" stroke-width="2"/></svg>
    </div>
    <div class="perk">
      <svg width="40" height="40" viewBox="0 0 40 40"><g fill="none" stroke="var(--blue)" stroke-width="2.5"><circle cx="20" cy="20" r="8"/><line x1="20" y1="2" x2="20" y2="7"/><line x1="20" y1="33" x2="20" y2="38"/><line x1="2" y1="20" x2="7" y2="20"/><line x1="33" y1="20" x2="38" y2="20"/></g></svg>
      <p class="perk-text">Daily yoga &amp; meditation to help fuel your ideas</p>
      <svg class="perk-dot" width="18" height="18" viewBox="0 0 18 18"><circle cx="9" cy="9" r="9" fill="var(--red)"/><path d="M7 5 L11 9 L7 13" fill="none" stroke="#fff" stroke-width="2"/></svg>
    </div>
    <div class="perk">
      <svg width="40" height="40" viewBox="0 0 40 40"><g fill="none" stroke="var(--blue)" stroke-width="2.5"><path d="M4 20 H36 A16 14 0 0 1 4 20 Z"/><line x1="12" y1="38" x2="28" y2="38"/><path d="M16 14 Q14 9 17 5"/><path d="M24 14 Q22 9 25 5"/></g></svg>
      <p class="perk-text">Three nutritious and delicious meals a day</p>
      <svg class="perk-dot" width="18" height="18" viewBox="0 0 18 18"><circle cx="9" cy="9" r="9" fill="var(--red)"/><path d="M7 5 L11 9 L7 13" fill="none" stroke="#fff" stroke-width="2"/></svg>
    </div>
    <div class="perk">
      <svg width="40" height="40" viewBox="0 0 40 40"><g fill="none" stroke="var(--blue)" stroke-width="2.5" stroke-linejoin="round"><path d="M4 6 H26 V20 H12 L6 25 V20 H4 Z"/><path d="M30 14 H36 V28 H34 V33 L28 28 H16 V24"/></g></svg>
      <p class="perk-text">Good, honest feedback, insight from attendees.</p>
      <svg class="perk-dot" width="18" height="18" viewBox="0 0 18 18"><circle cx="9" cy="9" r="9" fill="var(--red)"/><path d="M7 5 L11 9 L7 13" fill="none" stroke="#fff" stroke-width="2"/></svg>
    </div>
    <svg class="slider-arrow prev" width="20" height="30" viewBox="0 0 20 30"><polyline points="15,4 5,15 15,26" fill="none" stroke="var(--ink)" stroke-width="3"/></svg>
    <svg class="slider-arrow next" width="20" height="30" viewBox="0 0 20 30"><polyline points="5,4 15,15 5,26" fill="none" stroke="var(--ink)" stroke-width="3"/></svg>
  </div>
  <div class="divider"></div>
</section>

<section class="team">
  <h2 class="section-title">Meet Your Retreat Organisers</h2>
  <div class="team-row">
    <div class="member">
      <div class="member-photo one" role="img" aria-label="Portrait photo of organiser Tomas Varga"></div>
      <div>
        <div class="member-name">Tomas Varga</div>
        <p class="member-bio">A software engineer in London, who knows only too well the challenges…</p>
        <span class="member-link">Read more</span>
      </div>
    </div>
    <div class="member">
      <div class="member-photo two" role="img" aria-label="Portrait photo of organiser Lena Moreau"></div>
      <div>
        <div class="member-name">Lena Moreau</div>
        <p class="member-bio">An internationally-certified yoga teacher, who loves connecting with people…</p>
        <span class="member-link">Read more</span>
      </div>
    </div>
  </div>
</section>

<section class="feedback">
  <h2 class="feedback-title">What Do You Think?</h2>
  <p class="feedback-copy">Sound good? Want to know more? Share some feedback via the button below and we can keep the retreat in mind for you.</p>
  <span class="btn btn-red">Share your thoughts ➜</span>
</section>

<footer class="site-footer">
  <div class="contact">
    <span>(+44) 020 7946 0321</span><span class="sep"></span><span>hello@makershollow.co.uk</span>
  </div>
  <div class="legal">
    <span>Copyright © 2018 Makers’ Hollow. All Rights Reserved</span><span>|</span><span>Site Map</span>
  </div>
  <div class="social"><span></span><span></span><span></span><span></span><span></span><span></span></div>
</footer>

</body>
</html>
```